Computer consultant business card

Bexil Software is a newly started computer consulting company. It's a small one-man company that provides mostly Vornix applications but also websites in collaboration with designers. I'm running this company on the side of full time university studies.

I want the final design to be clean and memorable. Be creative! :)

Some inspiration:
http://www.pixelmarta.com/design/48317
http://www.pixelmarta.com/design/2739164/business-card-design-by-frostlynk
http://www.pixelmarta.com/design/604281/business-card-design-by-koralind-vestrabanu

See attachment for my company logo.
Updates

I would like to thank everyone for submitting! I'll need a couple of days to review and ultimately select a design.

Target Market(s)

Non-technical entrepreneurs and small companies.

Industry/Entity Type

University

Requirements
Must have
• My company logo.
In any way, both colors from my logo.
First- and last name, e-mail and phone number.
Double-sided design.
Nice to have
• Something creative with the symbol in my logo

```html
<!DOCTYPE html>
<html lang="en">
<head>
<meta charset="utf-8">
<title>Bexil Software – Business Card</title>
<link rel="stylesheet" href="https://fonts.googleapis.com/css2?family=Quicksand:wght@300;400;600&display=swap">
<style>
  :root {
    --brand-blue: #86e1fb;
    --brand-black: #060909;
    --ink: #0d1414;
    --bg-light: #6b7d7b;
    --bg-dark: #45525a;
    --divider: #c9d0d0;
  }
  html, body {
    margin: 0;
    padding: 0;
    overflow: hidden;
  }
  .canvas {
    position: relative;
    width: 1041px;
    height: 1200px;
    overflow: hidden;
    font-family: "Quicksand", sans-serif;
  }
  .card-side {
    position: absolute;
    left: 0;
    width: 1041px;
  }
  .card-front {
    top: 0;
    height: 600px;
    background: radial-gradient(ellipse 560px 420px at 525px 300px, var(--bg-light) 0%, var(--bg-dark) 100%);
  }
  .card-back {
    top: 601px;
    height: 599px;
    background: radial-gradient(ellipse 560px 420px at 525px 295px, var(--bg-light) 0%, var(--bg-dark) 100%);
  }
  .side-divider {
    position: absolute;
    top: 600px;
    left: 0;
    width: 1041px;
    height: 1px;
    background: linear-gradient(90deg, transparent 0%, var(--divider) 10%, var(--divider) 90%, transparent 100%);
  }
  .band {
    position: absolute;
    box-shadow: 0 4px 8px rgba(0, 0, 0, 0.55);
  }
  .band-black { background: var(--brand-black); }
  .band-blue { background: var(--brand-blue); }

  .front-band { left: 0; top: 233px; width: 795px; height: 132px; }
  .front-tile { left: 802px; top: 233px; width: 239px; height: 132px; }

  .brand-dot {
    position: absolute;
    left: 262px;
    top: 261px;
    width: 76px;
    height: 76px;
    border-radius: 50%;
    background: var(--brand-blue);
  }
  .brand-name {
    position: absolute;
    left: 379px;
    top: 228px;
    margin: 0;
    font-size: 112px;
    font-weight: 600;
    line-height: 132px;
    letter-spacing: -1px;
    color: var(--brand-blue);
  }

  .name-band { left: 0; top: 233px; width: 411px; height: 132px; }
  .back-tile { left: 802px; top: 233px; width: 239px; height: 132px; }
  .holder-name {
    position: absolute;
    left: 37px;
    top: 233px;
    margin: 0;
    font-size: 60px;
    font-weight: 300;
    line-height: 132px;
    color: var(--brand-blue);
    white-space: nowrap;
  }
  .contact {
    position: absolute;
    left: 428px;
    top: 243px;
    margin: 0;
    font-size: 24px;
    font-weight: 400;
    letter-spacing: -0.3px;
    color: var(--ink);
    line-height: 56px;
    white-space: nowrap;
  }
  .contact span { display: block; }
</style>
</head>
<body>
<div class="canvas">
  <section class="card-side card-front">
    <div class="band band-black front-band"></div>
    <div class="brand-dot"></div>
    <h1 class="brand-name">bexil</h1>
    <div class="band band-blue front-tile"></div>
  </section>

  <div class="side-divider"></div>

  <section class="card-side card-back">
    <div class="band band-black name-band"></div>
    <p class="holder-name">Your &nbsp;Name</p>
    <p class="contact">
      <span>Phone &nbsp;: &nbsp;1234567890</span>
      <span>Email &nbsp;: &nbsp;yourname@bexil.com</span>
    </p>
    <div class="band band-blue back-tile"></div>
  </section>
</div>
</body>
</html>
```